Vibrant, yet professional, stationery set and other designs required.

I need to source a fantastic designer for a new project as part of my company using a new logo designed via sketch harbor.

**UPDATE** I am not looking for just 'fine' design that will suffice. I am looking for something great.

We are a life assurance brokerage based in Dublin, Ireland and BrightRoost.ie is our new website aimed at providing services for young families in Ireland. We are hoping to be the 'Velro' level of service providers in this area and I am looking for the quality of design to reflect this :-) Hopefully that makes sense!

I have a preference for straight lines over curves and waves.

I need...

1. Business card
2. Letterhead
3. Banner (for printing - 76cm X 305cm)
4. Car branding for KORVA 9 (2014 sport model) I believe the templates are freely available online.

Target Market(s)

Parents in Ireland - Aged 27 to 50.

Industry/Entity Type

Financial Planning

Colors

Designer to choose colors to be used in the design.

Requirements
Must have
• All of the items listed in the description above. I like clean, bright, legible, vibrant and professional design.
Should not have
• No silly or 'cheap' looking designs. This is a professional company looking to provide a professional service.

```html
<!DOCTYPE html>
<html lang="en">
<head>
<meta charset="utf-8">
<title>BrightRoost.ie Business Card</title>
<link href="https://fonts.googleapis.com/css2?family=Roboto:wght@400;500&family=Roboto+Condensed:wght@400;700&display=swap" rel="stylesheet">
<style>
  :root {
    --backdrop: #e6e6e6;
    --card-white: #f4f4f4;
    --card-slate: #8e9a9d;
    --brand-green: #9bc541;
    --brand-grey: #8e9a9d;
    --text-dark: #4d4d4d;
    --white: #ffffff;
  }
  * { margin: 0; padding: 0; box-sizing: border-box; }
  html, body {
    width: 1200px;
    height: 960px;
    overflow: hidden;
    background: var(--backdrop);
    font-family: "Roboto", Arial, sans-serif;
  }
  .card {
    position: absolute;
    width: 600px;
    height: 341px;
  }
  .card-front { left: 302px; top: 130px; background: var(--card-white); }
  .card-back { left: 300px; top: 489px; background: var(--card-slate); }

  .name-band {
    position: absolute;
    left: 0;
    top: 47px;
    width: 363px;
    height: 59px;
    background: var(--brand-green);
    color: var(--white);
    font-family: "Roboto Condensed", Arial, sans-serif;
    padding: 7px 0 0 30px;
  }
  .person-name { font-size: 23px; font-weight: 700; line-height: 26px; }
  .person-role { font-size: 15px; font-weight: 700; line-height: 18px; }

  .wordmark {
    position: absolute;
    display: flex;
    align-items: center;
    gap: 8px;
    font-family: "Roboto", Arial, sans-serif;
    font-weight: 500;
    letter-spacing: -0.5px;
  }
  .wordmark-dot { border-radius: 50%; flex: none; }
  .card-front .wordmark {
    right: 32px;
    top: 58px;
    color: var(--brand-grey);
    font-size: 34px;
  }
  .card-front .wordmark-dot { width: 14px; height: 14px; background: var(--brand-grey); }
  .card-back .wordmark {
    left: 0;
    right: 0;
    top: 138px;
    justify-content: center;
    color: var(--white);
    font-size: 54px;
  }
  .card-back .wordmark-dot { width: 20px; height: 20px; background: var(--white); }

  .contact-list {
    position: absolute;
    left: 30px;
    top: 237px;
    list-style: none;
    color: var(--text-dark);
    font-size: 14px;
    line-height: 19px;
  }
  .contact-list li { display: flex; align-items: center; gap: 9px; }
  .contact-icon { width: 12px; height: 12px; fill: var(--brand-green); flex: none; }

  .address {
    position: absolute;
    right: 31px;
    top: 254px;
    text-align: right;
    font-style: normal;
    color: var(--text-dark);
    font-size: 14px;
    line-height: 19px;
  }
</style>
</head>
<body>
  <section class="card card-front">
    <div class="name-band">
      <div class="person-name">Liam Carver</div>
      <div class="person-role">CEO/Founder</div>
    </div>
    <div class="wordmark"><span class="wordmark-dot"></span>BrightRoost.ie</div>

    <ul class="contact-list">
      <li>
        <svg class="contact-icon" viewBox="0 0 12 12" aria-hidden="true"><path d="M2.5 0.5 L4.5 0.5 L5.2 3 L3.8 4.2 Q5 7 7.8 8.2 L9 6.8 L11.5 7.5 L11.5 9.5 Q11 11.5 9 11.5 Q0.5 10.5 0.5 2.5 Q0.5 0.5 2.5 0.5 Z"/></svg>
        614 502 7183
      </li>
      <li>
        <svg class="contact-icon" viewBox="0 0 12 12" aria-hidden="true"><path d="M3 0 H9 V12 H3 Z M4 1.5 V9.5 H8 V1.5 Z M5.5 10.2 H6.5 V11.2 H5.5 Z" fill-rule="evenodd"/></svg>
        852 319 4076
      </li>
      <li>
        <svg class="contact-icon" viewBox="0 0 12 12" aria-hidden="true"><path d="M3 0.5 H9 V4 H3 Z M0.5 4.5 H11.5 V9.5 H0.5 Z M2.5 8 H9.5 V11.5 H2.5 Z"/></svg>
        497 260 3815
      </li>
      <li>
        <svg class="contact-icon" viewBox="0 0 12 12" aria-hidden="true"><path d="M0.5 2 H11.5 V3 L6 6.5 L0.5 3 Z M0.5 4.2 L6 7.7 L11.5 4.2 V10 H0.5 Z"/></svg>
        liam@brightroost.com
      </li>
    </ul>

    <address class="address">
      2214 Hollow Birch Road<br>
      Kestrel Bay, Alaska 34019<br>
      www.brightroost.com
    </address>
  </section>

  <section class="card card-back">
    <div class="wordmark"><span class="wordmark-dot"></span>BrightRoost.ie</div>
  </section>
</body>
</html>
```